Label design for organic saffron, saffron and herbal syrup

We cultivate saffron, Damszen roses, flowers and herbs. We would need a recognizable outfit (label) for our products. Theoretically (and practically) we have "converted" the family coat of arms into a kind of LOGO. I would send this in the attachment. It would be nice if - in one way or another - this LOGO / coat of arms could be used (certainly with other colors). For some time we have played with the idea of changing the second part of the family name "Wallmoser" (in German .... greuth sounds similar to Kraut / herb [English]) .... eg Wallmoser's saffron syrup into the labeling.
Our products are primarily syrups, currently herbal syrup and saffron syrup. Here the first problem arises, the only bottles / caps that are actually approved for syrup filling (hot filling) are appallingly ugly (see attachment), the only possibility of "sprucing up" is to use so-called "shrink sleeves" (here we need a diameter of 31 and a length of about 40), the colors of which are also limited. Besides the syrup, we sell saffron as a spice and various herbal mixtures (see appendix current packaging saffron). Our quantities are small (syrup 200ml-330ml), saffron in the gram range.
We also need quasi the back of the labeling (this should be able to be redefined per charge) .... Batch 1 (with small quantity has eg more of herb xy than the next batch or the saffron syrup with batch xy needs more / less saffron). In addition, we are certified organic (for this reason, the reverse side would also have to contain all the requirements of organic labeling) [see attachment].
We do not really want to address a specific clientele. Maybe just people who want to taste, enjoy, mix drinks, cook .... (and - unfortunately - don't like Corvel syrup :-) and want to pay a bit more, or find our saffron or herbs better than others) .
In summary
- Strong recognition value (possibly inclusion of "coat of arms", color variable ... although I personally don't like yellow that much)
- Saffron syrup (the color of the saffron syrup is yellow / golden-yellow-light orange, in a transparent ugly bottle)
- Herbal syrup (color variable from blue / green / brown / red elements, in transparent ugly bottle)
Saffron and other herbs (very small containers, type of container not yet fixed)
Regarding a potential "style" I can unfortunately give little information. On the one hand, I am in love with minimalism, on the other hand, I find the translucent, cryptic, implied enormously attractive and sometimes even the "overloaded" colorful has its charm. I think that all in all, it just has to be coherent, and then it will be good.
Requirements
Must have
- Integration of Code of Arms, modifiable for different products

```html
<!DOCTYPE html>
<html lang="de">
<head>
<meta charset="utf-8">
<title>Wallmoser Rose Sirup – Etikett</title>
<link rel="stylesheet" href="https://fonts.googleapis.com/css2?family=Open+Sans:wdth,wght@75,700&family=Playfair+Display:wght@400;500&display=swap">
<style>
  :root {
    --plum: #8a1a52;
    --plum-deep: #6e1442;
    --gold: #c9a24a;
    --gold-light: #ecd58e;
    --gold-dark: #9a7426;
    --cream: #fdf1cc;
    --navy: #2b2a6e;
    --ink: #2a2a2a;
    --paper: #ffffff;
    --bio-green: #c8e0a0;
    --bio-leaf: #7ab648;
  }
  html, body {
    margin: 0;
    padding: 0;
    width: 878px;
    height: 1200px;
    overflow: hidden;
    background: var(--paper);
  }
  .label {
    display: block;
    width: 878px;
    height: 1200px;
  }
  .info-text {
    font-family: "Open Sans", Arial, sans-serif;
    font-stretch: 75%;
    font-weight: 700;
    font-size: 11.5px;
    fill: var(--ink);
  }
  .volume {
    font-family: "Open Sans", Arial, sans-serif;
    font-stretch: 75%;
    font-weight: 700;
    font-size: 19px;
    fill: #333;
  }
  .best-before {
    font-family: "Open Sans", Arial, sans-serif;
    font-weight: 700;
    font-size: 14px;
    fill: #111;
  }
  .brand-name {
    font-family: "Playfair Display", Georgia, serif;
    font-weight: 400;
    font-size: 38px;
    fill: var(--navy);
  }
  .product-name {
    font-family: "Playfair Display", Georgia, serif;
    font-weight: 500;
    font-size: 60px;
    fill: #ffffff;
    stroke: #1d0a14;
    stroke-width: 2.2px;
    paint-order: stroke;
  }
</style>
</head>
<body>
<svg class="label" viewBox="0 0 683 934" preserveAspectRatio="none" xmlns="http://www.w3.org/2000/svg">
  <defs>
    <linearGradient id="ornamentFill" x1="0" y1="0" x2="1" y2="1">
      <stop offset="0" stop-color="#8e1d56"/>
      <stop offset="0.5" stop-color="#82194d"/>
      <stop offset="1" stop-color="#8e2a55"/>
    </linearGradient>
    <linearGradient id="goldBand" x1="0" y1="0" x2="0" y2="1">
      <stop offset="0" stop-color="var(--gold-light)"/>
      <stop offset="0.5" stop-color="var(--gold)"/>
      <stop offset="1" stop-color="var(--gold-dark)"/>
    </linearGradient>
    <linearGradient id="bannerFill" x1="0" y1="0" x2="0" y2="1">
      <stop offset="0" stop-color="var(--plum)"/>
      <stop offset="1" stop-color="var(--plum-deep)"/>
    </linearGradient>
  </defs>

  <!-- label body -->
  <rect class="label-body" x="38" y="38" width="607" height="854" fill="var(--cream)"/>

  <!-- top band with ornamental gold pattern area -->
  <rect class="ornament-band" x="38" y="38" width="607" height="300" fill="url(#ornamentFill)"
        role="img" aria-label="Gold paisley and floral ornament on plum ground"/>

  <!-- crest medallion: neck and circle -->
  <path class="crest-medallion"
        d="M295,38 L388,38 L388,73 A150,150 0 1 1 295,73 Z"
        fill="var(--paper)" stroke="var(--gold)" stroke-width="3"/>

  <!-- brand name in medallion -->
  <text class="brand-name" x="341" y="288" text-anchor="middle">Wallmoser</text>

  <!-- gold band -->
  <rect class="gold-band" x="38" y="330" width="607" height="28" fill="url(#goldBand)"/>

  <!-- product banner -->
  <path class="product-banner"
        d="M210,358 L472,358 L472,570 A131,131 0 0 1 210,570 Z"
        fill="url(#bannerFill)" stroke="var(--gold)" stroke-width="3"
        role="img" aria-label="Faint line drawing of a rose on the plum banner"/>

  <text class="product-name" x="341" y="488" text-anchor="middle">Rose</text>
  <text class="product-name" x="341" y="553" text-anchor="middle">Sirup</text>

  <!-- ingredients column -->
  <g class="ingredients" transform="translate(0,612)">
    <text class="info-text" transform="translate(75,0) rotate(-90)" text-anchor="middle">ZUTATEN: Lorem ipsum dolor sit amet, consectetur adipiscing elit.</text>
    <text class="info-text" transform="translate(89,0) rotate(-90)" text-anchor="middle">Morbi ultricies molestie orci. Aenean purus mauris, sodales nec</text>
    <text class="info-text" transform="translate(103,0) rotate(-90)" text-anchor="middle">diam dignissim, porttitor laoreet enim. Aliquam id sollicitudin</text>
    <text class="info-text" transform="translate(117,0) rotate(-90)" text-anchor="middle">turpis. Vivamus aliquet elit sem, et ornare ex aliquam in.</text>
  </g>

  <!-- producer column -->
  <g class="producer">
    <text class="info-text" transform="translate(567,690) rotate(-90)">*aus kontrolliert biologischer Landwirtschaft</text>
    <text class="info-text" transform="translate(585,690) rotate(-90)">Expertly crafted by: Halden-Wallmoser</text>
    <text class="info-text" transform="translate(599,690) rotate(-90)">1234 Street Name, Any City, District, Country</text>
  </g>

  <!-- best before box -->
  <rect class="best-before-box" x="548" y="697" width="70" height="161" fill="var(--paper)" stroke="#111" stroke-width="1.2"/>
  <text class="best-before" transform="translate(574,850) rotate(-90)">Best Before:</text>

  <!-- organic certification badge (plain shapes) -->
  <g class="organic-badge">
    <rect x="303" y="721" width="73" height="145" fill="var(--bio-green)" stroke="#8fb86a" stroke-width="1"/>
    <rect x="307" y="725" width="65" height="45" fill="var(--paper)"/>
    <circle cx="339.5" cy="747.5" r="19" fill="none" stroke="#2f8a3a" stroke-width="3"/>
    <rect x="307" y="775" width="65" height="43" fill="var(--bio-leaf)"/>
  </g>

  <!-- volume and dilution -->
  <text class="volume" x="228" y="866">200mL</text>
  <text class="volume" x="397" y="866">1:7</text>
</svg>
</body>
</html>
```